Business Card for a Dental Office

The design should communicate integrity, quality and reliability. We also want the card look elegant, simple, but still stand out, different from the traditional-dental-office business card.

Industry/Entity Type

Business

```html
<!DOCTYPE html>
<html lang="en">
<head>
<meta charset="utf-8">
<title>Halvern Dental Centre – Business Card</title>
<link rel="stylesheet" href="https://fonts.googleapis.com/css2?family=Oswald:wght@600&family=Open+Sans:wght@400;700&display=swap">
<style>
  :root {
    --page: #8a7355;
    --card-top: #1c1c1c;
    --card-bottom: #050505;
    --white: #f4f4f4;
    --gold: #c9b21f;
    --rule: #d8d8d8;
    --muted: #e6e6e6;
  }
  * { margin: 0; padding: 0; box-sizing: border-box; }
  html, body {
    width: 1200px; height: 1022px; overflow: hidden;
    background: var(--page);
  }
  .card {
    position: absolute;
    left: 110px; top: 231px;
    width: 980px; height: 560px;
    background: linear-gradient(160deg, var(--card-top) 0%, var(--card-bottom) 60%);
    border-radius: 3px;
    box-shadow: 0 18px 40px rgba(0,0,0,0.45);
    font-family: "Open Sans", sans-serif;
    color: var(--white);
  }
  .brand {
    position: absolute; left: 70px; top: 62px;
    display: flex; align-items: center; gap: 18px;
  }
  .brand-mark {
    width: 74px; height: 74px; background: var(--gold);
  }
  .brand-name {
    font-family: "Oswald", sans-serif; font-weight: 600;
    font-size: 46px; line-height: 1; letter-spacing: 0.5px;
    text-transform: uppercase; color: var(--white);
  }
  .brand-tagline {
    margin-top: 6px;
    font-family: "Oswald", sans-serif; font-weight: 600;
    font-size: 19px; letter-spacing: 1px; text-transform: uppercase;
    color: var(--gold);
  }
  .divider {
    position: absolute; left: 470px; right: 0; top: 300px;
    height: 1px; background: var(--rule);
  }
  .contact {
    position: absolute; left: 70px; bottom: 60px;
  }
  .person-name {
    font-weight: 700; font-size: 40px; letter-spacing: 0.5px;
    text-transform: uppercase; line-height: 1.1;
  }
  .person-role {
    display: flex; align-items: center; gap: 12px;
    color: var(--gold); font-size: 20px; letter-spacing: 1px;
    text-transform: uppercase; margin: 4px 0 14px;
  }
  .person-role::after {
    content: ""; width: 140px; height: 1px; background: var(--rule);
  }
  .contact-list { list-style: none; }
  .contact-item {
    display: flex; align-items: center; gap: 14px;
    font-size: 24px; line-height: 1.35; color: var(--muted);
  }
  .contact-icon { width: 18px; height: 18px; flex: none; }
</style>
</head>
<body>
  <section class="card">
    <header class="brand">
      <div class="brand-mark"></div>
      <div>
        <div class="brand-name">Halvern Dental Centre</div>
        <div class="brand-tagline">Care you can trust in every smile</div>
      </div>
    </header>

    <div class="divider"></div>

    <div class="contact">
      <div class="person-name">Marlo Quintero</div>
      <div class="person-role">Director</div>
      <ul class="contact-list">
        <li class="contact-item">
          <svg class="contact-icon" viewBox="0 0 24 24" aria-hidden="true">
            <path fill="#c9b21f" d="M6.6 10.8a15 15 0 0 0 6.6 6.6l2.2-2.2c.3-.3.7-.4 1-.2 1.1.4 2.3.6 3.6.6.6 0 1 .4 1 1V20c0 .6-.4 1-1 1C10.6 21 3 13.4 3 4c0-.6.4-1 1-1h3.5c.6 0 1 .4 1 1 0 1.3.2 2.5.6 3.6.1.3 0 .7-.2 1z"/>
          </svg>
          +330 5518-2094
        </li>
        <li class="contact-item">
          <svg class="contact-icon" viewBox="0 0 24 24" aria-hidden="true">
            <rect x="2" y="5" width="20" height="14" fill="none" stroke="#c9b21f" stroke-width="2"/>
            <path d="M2 6l10 7 10-7" fill="none" stroke="#c9b21f" stroke-width="2"/>
          </svg>
          info@halverndentalcentre.com
        </li>
        <li class="contact-item">
          <svg class="contact-icon" viewBox="0 0 24 24" aria-hidden="true">
            <circle cx="12" cy="12" r="10" fill="none" stroke="#c9b21f" stroke-width="2"/>
            <path d="M2 12h20M12 2c3 3 3 17 0 20M12 2c-3 3-3 17 0 20" fill="none" stroke="#c9b21f" stroke-width="1.6"/>
          </svg>
          www.halverndentalcentre.com
        </li>
      </ul>
    </div>
  </section>
</body>
</html>
```